Web Design job - NetKestrel Company including Desktop & Mobile version

Create a Web Design (Uncoded - PSD layout only)

1. About our company

NetKestrel is an Australian-based company which sells used networking devices to coporates and other brokers in USA, Europe and other countries. We are the market leader in this space and currently have warehouses in Sydney and California. Most of our products are from VORLAN.

Our competitive advantages come from lowest price in the market, flexible product configuration for different demands of customers, long time experience in the business and huge stock of inventory.

We are in need of a new website to enhance customer and partner engagement which are measured by sales metrics and website performance metrics such as number of request for a quote, number of new orders, return visits, views, conversion rate, etc.

2. Website structure:

We need different looks for different devices: Desktop, iPad and Mobile with popular screen resolutions for each of following page.

Try to make one as good as possible, then we can move further. Below are the main pages of the web:

+ Home Page: Where customers learn about the company and its business. Should have: Beautiful company profile, highlighted company contact and strengths; A comprehensive overview about selling products.

+ Category Page: Where customers learn about products in a category and do the search action. Should focus on filter and sort functions for easily finding a product.

+ Product Page: Where customers learn about the details of a specific products such as price, image, description, related products.
- Also need features for cross-sell or up-sell.
- An item may have both new and refurbished prices, or either or none of them. Should have options to choose between new or refurbished price to add to cart.

+ Information Page: About the company, Company Announcement.

+ Cart management and Check-out

+ Search results

REFERENCES
Current website: http://netkestrel.com.au/

Prefered Layout:
- https://www.gearbazaar-example.com/en/vorlan-systems/vorlan-router-series/vorlan-series-1900/vorlan-systems-vorlan1941-k9
- https://www.wiresandboxes-example.com/vorlan-2port-rj48-multiflex-t1-trunk-card-vwic2mftt1-p-1374.html
- The attached files play as wireframes, only for the purpose of guiding. You are free to make your choices of colors and layouts.

Target Market(s)

- Corporate clients
- Main market: Australia

Industry/Entity Type

It Company

Number of Pages Required

3 page

Font styles to use
Sans Serif

Requirements
Must have
• - The new design should have a clear look to easily find information while should look professional to aim at corporate clients.
• - Require least time or effort to finish a task
• - Optimize for SEO and loading time
• - Mobile version is optimized for touching, swiping and loading time.
• - Bear in mind that the new website need minimum effort of manual tasks such as updating content. We don’t have human resources for these yet.
Nice to have
• - Should have design for each scenario such as click, popup, dropdown, deactive, have/not have an object

```html
<!DOCTYPE html>
<html lang="en">
<head>
<meta charset="utf-8">
<title>NetKestrel – Networking Equipment</title>
<link href="https://fonts.googleapis.com/css2?family=Lato:wght@300;400;700;900&display=swap" rel="stylesheet">
<style>
:root{
  --orange:#f58a2b;
  --navy:#1f4e96;
  --ink:#2b2b2b;
  --muted:#666;
  --charcoal:#3a3a3a;
  --hero-bg:#efeeec;
  --panel-grey:#ececec;
  --line:#d9d9d9;
  --red:#e2262b;
  --teal:#7ecfc7;
  --lime:#c4e08f;
  --peach:#f8c48b;
  --footer:#e4e4e4;
  --sky:#cfe0ee;
}
*{box-sizing:border-box;margin:0;padding:0}
html,body{width:1200px;height:3462px;overflow:hidden;background:#fff}
body{font-family:'Lato',sans-serif;color:var(--ink);position:relative}
.abs{position:absolute}
svg{display:block}

.brand{left:88px;top:26px;display:flex;align-items:center;gap:12px}
.brand-dot{width:44px;height:44px;border-radius:50%;background:var(--orange)}
.brand-name{font-size:30px;font-weight:900;color:var(--navy)}
.search{left:330px;top:30px;width:203px;height:42px;border:2px solid #5fa8d6;display:flex;align-items:center;justify-content:space-between;padding:0 12px;font-size:13px;color:#888}
.contact{top:42px;display:flex;align-items:center;gap:10px;font-size:13px;color:var(--ink)}
.cart{left:1028px;top:34px;display:flex;align-items:center;gap:10px;font-size:14px}

.nav{left:0;top:104px;width:1200px;height:44px;background:var(--orange)}
.nav-home{position:absolute;left:84px;top:13px}
.nav a{position:absolute;top:15px;color:#fff;font-size:13px;letter-spacing:.3px;text-decoration:none}
.quote-btn{position:absolute;left:944px;top:6px;width:170px;height:32px;background:#111;color:#fff;font-size:13px;font-weight:700;display:flex;align-items:center;justify-content:center;gap:22px}

.hero{left:0;top:148px;width:1200px;height:438px;background:var(--hero-bg)}
.hero-visual{left:88px;top:105px;width:364px;height:237px;background:linear-gradient(135deg,#5a5e66,#2a2c31 60%,#9a9ea6)}
.hero-title{left:512px;top:130px;font-size:50px;font-weight:900;color:var(--navy);letter-spacing:.5px}
.hero-sub{left:512px;top:204px;font-size:18px;color:var(--navy)}
.hero-btn{left:512px;top:244px;width:162px;height:50px;background:var(--orange);color:#fff;font-weight:900;font-size:17px;display:flex;align-items:center;justify-content:center}
.dots{left:512px;top:317px;display:flex;gap:8px}
.dots span{width:18px;height:18px;border-radius:50%;border:2px solid #777}
.dots span.on{border-color:var(--orange);background:radial-gradient(var(--orange) 40%,transparent 45%)}

.section-title{width:1200px;left:0;text-align:center;font-size:33px;font-weight:400;color:var(--orange);letter-spacing:.5px}

.cat{top:739px;width:243px;height:247px;border:1px solid var(--line)}
.cat-img{position:absolute;left:30px;top:30px;width:183px;height:130px;background:linear-gradient(160deg,#d8dadd,#3c3f44)}
.cat-label{position:absolute;left:-1px;bottom:-1px;width:243px;height:42px;background:var(--charcoal);color:#fff;font-size:16px;font-weight:700;display:flex;align-items:center;justify-content:center}
.cat.active .cat-label{background:var(--orange)}
.cat.active .cat-label::after{content:"";position:absolute;left:112px;bottom:-12px;border:12px solid transparent;border-bottom:0;border-top-color:var(--orange)}

.row{left:88px;width:1024px;height:220px;display:flex}
.prod{flex:1;position:relative;text-align:center}
.row.divided .prod+.prod{border-left:1px solid var(--line)}
.prod-img{width:130px;height:100px;margin:10px auto 0;background:linear-gradient(150deg,#cfd2d6,#44474d)}
.prod-img.board{background:linear-gradient(150deg,#7fb06a,#2f5b2a)}
.prod-name{margin-top:32px;font-size:15px;color:var(--ink)}
.price{margin-top:6px;font-size:15px}
.price s{color:var(--muted);margin-right:10px}
.price b{color:var(--red);font-weight:400}
.add{margin:12px auto 0;width:88px;height:28px;background:var(--charcoal);color:#fff;font-size:12px;display:flex;align-items:center;justify-content:center}

.promo{left:88px;top:1343px;width:1024px;height:180px;border:9px solid var(--orange);background:var(--panel-grey)}
.promo-kicker{left:125px;top:40px;font-size:16px;color:var(--ink)}
.promo-title{left:125px;top:62px;font-size:36px;color:var(--ink)}
.promo-btn{left:125px;top:110px;width:78px;height:28px;background:var(--charcoal);color:#fff;font-size:13px;display:flex;align-items:center;justify-content:center}
.promo-visual{left:665px;top:20px;width:200px;height:120px;background:linear-gradient(150deg,#6f9d5c,#1e3d1a)}
.promo-shadow{left:100px;top:1530px;width:1000px;height:50px;background:radial-gradient(ellipse at top,rgba(0,0,0,.22),transparent 70%)}

.arrows{left:1062px;display:flex;gap:12px}

.welcome{left:0;top:2001px;width:600px;height:487px;background:var(--orange);color:#fff}
.welcome h2{position:absolute;left:88px;top:38px;font-size:32px;font-weight:400}
.facts{position:absolute;left:88px;top:110px;list-style:none}
.facts li{display:flex;align-items:center;gap:18px;font-size:17px;font-weight:700;height:40px}
.welcome p{position:absolute;left:88px;top:290px;width:450px;font-size:13px;line-height:19px}
.welcome .more{position:absolute;left:88px;top:428px;font-size:13px}
.quote{left:600px;top:2001px;width:600px;height:487px;background:linear-gradient(100deg,#dfe9f2,var(--sky) 55%,#b9cfe2)}
.quote-photo{position:absolute;right:0;top:0;width:265px;height:487px;background:linear-gradient(90deg,rgba(190,160,140,0),rgba(150,110,90,.45))}
.quote h2{position:absolute;left:18px;top:38px;font-size:32px;font-weight:400;color:var(--orange)}
.quote .phone{position:absolute;left:18px;top:112px;font-size:34px;font-weight:700;color:#111}
.quote .note{position:absolute;left:18px;top:172px;width:310px;font-size:15px;line-height:20px;color:#111}
.quote .or{position:absolute;left:18px;top:232px;font-size:15px;color:#111}
.quote .mail{position:absolute;left:18px;top:272px;font-size:30px;font-weight:700;color:#111}

.strip{top:2943px;width:400px;height:131px;display:flex;align-items:center;justify-content:center;gap:22px;font-size:28px;color:var(--ink)}

.footer{left:0;top:3074px;width:1200px;height:388px;background:var(--footer)}
.fcol{top:44px;font-size:12px;color:var(--ink);line-height:17px}
.fcol h3{font-size:16px;font-weight:700;margin-bottom:24px;letter-spacing:.3px}
.fline{display:flex;align-items:center;gap:8px;margin-bottom:8px}
.cards{display:grid;grid-template-columns:repeat(3,38px);gap:8px}
.cards span{height:26px;border-radius:3px;background:#fff;border:1px solid #c8c8c8}
.why li{list-style:none;display:flex;align-items:center;gap:12px;font-size:11px;font-weight:700;margin-bottom:15px;text-transform:uppercase}
.rule{left:88px;top:318px;width:1024px;height:1px;background:#c9c9c9}
.copy{left:88px;top:341px;font-size:12px}
</style>
</head>
<body>

<header>
  <div class="abs brand"><span class="brand-dot"></span><span class="brand-name">NetKestrel</span></div>
  <div class="abs search"><span>Search products</span>
    <svg width="16" height="16" viewBox="0 0 16 16"><circle cx="6.5" cy="6.5" r="4.5" fill="none" stroke="#2d8ccc" stroke-width="2"/><path d="M10 10l4 4" stroke="#2d8ccc" stroke-width="2"/></svg></div>
  <div class="abs contact" style="left:690px">
    <svg width="14" height="14" viewBox="0 0 24 24"><path d="M6 2l4 4-2 3c1 3 4 6 7 7l3-2 4 4-3 4C10 22 2 14 2 5z" fill="#222"/></svg>(61) 02 5550 1427</div>
  <div class="abs contact" style="left:855px">
    <svg width="16" height="12" viewBox="0 0 16 12"><rect width="16" height="12" fill="#222"/><path d="M0 0l8 7 8-7" fill="none" stroke="#fff" stroke-width="1.3"/></svg>sales@netkestrel.com.au</div>
  <div class="abs cart">
    <svg width="30" height="26" viewBox="0 0 30 26"><path d="M1 3h5l4 14h15l3-10H8" fill="none" stroke="var(--orange)" stroke-width="2.5"/><circle cx="12" cy="22" r="2.5" fill="var(--orange)"/><circle cx="23" cy="22" r="2.5" fill="var(--orange)"/></svg>Cart(0)</div>
</header>

<nav class="abs nav">
  <svg class="nav-home" width="18" height="16" viewBox="0 0 18 16"><path d="M9 0l9 8h-3v8h-4v-5H7v5H3V8H0z" fill="#fff"/></svg>
  <a style="left:162px">ROUTERS</a>
  <a style="left:282px">SWITCHES</a>
  <a style="left:404px">WIRELESSES</a>
  <a style="left:540px">IP PHONES</a>
  <a style="left:668px">ACCESSORIES</a>
  <div class="quote-btn">Request a Quote <svg width="10" height="6" viewBox="0 0 10 6"><path d="M0 0h10L5 6z" fill="#fff"/></svg></div>
</nav>

<section class="abs hero">
  <div class="abs hero-visual" role="img" aria-label="Server racks and networking equipment"></div>
  <h1 class="abs hero-title">SAVE UP TO 40%</h1>
  <p class="abs hero-sub">By doing business with NETKESTREL</p>
  <div class="abs hero-btn">STOCK LIST &gt;</div>
  <div class="abs dots"><span class="on"></span><span></span><span></span></div>
</section>

<h2 class="abs section-title" style="top:668px">PRODUCT CATEGORIES</h2>
<div class="abs cat active" style="left:86px"><div class="cat-img" role="img" aria-label="Wireless access points and routers"></div><div class="cat-label">Wireless &amp; Securities</div></div>
<div class="abs cat" style="left:347px"><div class="cat-img" role="img" aria-label="Routers and switches"></div><div class="cat-label">Routers &amp; Switches</div></div>
<div class="abs cat" style="left:609px"><div class="cat-img" role="img" aria-label="IP desk phones"></div><div class="cat-label">IP Phones</div></div>
<div class="abs cat" style="left:870px"><div class="cat-img" role="img" aria-label="Transceiver modules and accessories"></div><div class="cat-label">Accessories</div></div>

<div class="abs row" style="top:1040px">
  <div class="prod"><div class="prod-img" role="img" aria-label="Wireless access point"></div><div class="prod-name">NKV2-16 Refurbished</div><div class="price"><s>$255</s><b>$195</b></div><div class="add">Add To Cart</div></div>
  <div class="prod"><div class="prod-img" role="img" aria-label="Rack router"></div><div class="prod-name">Refurbished</div><div class="price"><s>$255</s><b>$195</b></div><div class="add">Add To Cart</div></div>
  <div class="prod"><div class="prod-img" role="img" aria-label="Desktop router"></div><div class="prod-name">NKV2-16</div><div class="price"><s>$255</s><b>$195</b></div><div class="add">Add To Cart</div></div>
  <div class="prod"><div class="prod-img" role="img" aria-label="Rack router"></div><div class="prod-name">NKV Refurbished</div><div class="price"><s>$255</s><b>$195</b></div><div class="add">Add To Cart</div></div>
  <div class="prod"><div class="prod-img" role="img" aria-label="Small office router"></div><div class="prod-name">NKV8 Refurbished</div><div class="price"><s>$255</s><b>$195</b></div><div class="add">Add To Cart</div></div>
</div>

<section class="abs promo">
  <div class="abs promo-kicker">NKA-APX-102-R9 Refurbished</div>
  <div class="abs promo-title">Get 50% Off</div>
  <div class="abs promo-btn">Shop &gt;</div>
  <div class="abs promo-visual" role="img" aria-label="Network interface circuit board"></div>
</section>
<div class="abs promo-shadow"></div>

<h2 class="abs section-title" style="top:1603px">MOST SALE/ MOST VIEWED</h2>
<div class="abs arrows" style="top:1611px">
  <svg width="14" height="24" viewBox="0 0 14 24"><path d="M12 2L3 12l9 10" fill="none" stroke="var(--orange)" stroke-width="4"/></svg>
  <svg width="14" height="24" viewBox="0 0 14 24"><path d="M2 2l9 10-9 10" fill="none" stroke="var(--orange)" stroke-width="4"/></svg>
</div>
<div class="abs row divided" style="top:1692px">
  <div class="prod"><div class="prod-img" role="img" aria-label="Wireless access point"></div><div class="prod-name">NKV2-16 Refurbished</div><div class="price"><s>$255</s><b>$195</b></div><div class="add">Add To Cart</div></div>
  <div class="prod"><div class="prod-img" role="img" aria-label="Rack router"></div><div class="prod-name">Refurbished</div><div class="price"><s>$255</s><b>$195</b></div><div class="add">Add To Cart</div></div>
  <div class="prod"><div class="prod-img" role="img" aria-label="Desktop router"></div><div class="prod-name">NKV2-16</div><div class="price"><s>$255</s><b>$195</b></div><div class="add">Add To Cart</div></div>
  <div class="prod"><div class="prod-img" role="img" aria-label="Rack router"></div><div class="prod-name">NKV Refurbished</div><div class="price"><s>$255</s><b>$195</b></div><div class="add">Add To Cart</div></div>
  <div class="prod"><div class="prod-img" role="img" aria-label="Small office router"></div><div class="prod-name">NKV8 Refurbished</div><div class="price"><s>$255</s><b>$195</b></div><div class="add">Add To Cart</div></div>
</div>

<section class="abs welcome">
  <h2>Welcome to NETKESTREL</h2>
  <ul class="facts">
    <li><svg width="14" height="14"><circle cx="7" cy="7" r="6" fill="#fff"/></svg>7 Years of Experience</li>
    <li><svg width="16" height="14" viewBox="0 0 16 14"><path d="M1 1h10v7H5l-3 3V8H1z M12 4h3v7h-1v2l-2-2H7V9h5z" fill="#fff"/></svg>99.5% Positive Feedback on MarketLane</li>
    <li><svg width="18" height="14" viewBox="0 0 18 14"><circle cx="9" cy="4" r="3" fill="#fff"/><path d="M3 14c0-4 3-6 6-6s6 2 6 6z" fill="#fff"/></svg>300 Clients &amp; Partners Around the world</li>
    <li><svg width="12" height="14" viewBox="0 0 12 14"><path d="M0 0h8l4 4v10H0z" fill="#fff"/></svg>1,250 SKUs in Inventory</li>
  </ul>
  <p>Lorem Ipsum is simply dummy text of the printing and typesetting industry. Lorem Ipsum has been the industry's standard dummy text ever since the 1500s, when an unknown printer took a galley of type and scrambled it to make a type specimen book. It has survived not only five centuries, but also the leap into electronic typesetting, remaining essentially unchanged.</p>
  <div class="more">Read More &gt;</div>
</section>
<section class="abs quote">
  <div class="quote-photo" role="img" aria-label="Customer support agent wearing a headset"></div>
  <h2>Request a Quote</h2>
  <div class="phone">(061) 02 5550 1427</div>
  <div class="note">Call today for a great price on new and used networking equipment</div>
  <div class="or">OR email to:</div>
  <div class="mail">sales@netkestrel.com.au</div>
</section>

<h2 class="abs section-title" style="top:2551px">NEW PRODUCTS</h2>
<div class="abs arrows" style="top:2559px">
  <svg width="14" height="24" viewBox="0 0 14 24"><path d="M12 2L3 12l9 10" fill="none" stroke="var(--orange)" stroke-width="4"/></svg>
  <svg width="14" height="24" viewBox="0 0 14 24"><path d="M2 2l9 10-9 10" fill="none" stroke="var(--orange)" stroke-width="4"/></svg>
</div>
<div class="abs row divided" style="top:2640px">
  <div class="prod"><div class="prod-img board" role="img" aria-label="Memory module"></div><div class="prod-name">NKV2-16 Refurbished</div><div class="price"><s>$255</s><b>$195</b></div><div class="add">Add To Cart</div></div>
  <div class="prod"><div class="prod-img board" role="img" aria-label="Memory module"></div><div class="prod-name">Refurbished</div><div class="price"><s>$255</s><b>$195</b></div><div class="add">Add To Cart</div></div>
  <div class="prod"><div class="prod-img board" role="img" aria-label="Interface card"></div><div class="prod-name">NKV2-16</div><div class="price"><s>$255</s><b>$195</b></div><div class="add">Add To Cart</div></div>
  <div class="prod"><div class="prod-img board" role="img" aria-label="Voice module"></div><div class="prod-name">NKV Refurbished</div><div class="price"><s>$255</s><b>$195</b></div><div class="add">Add To Cart</div></div>
  <div class="prod"><div class="prod-img board" role="img" aria-label="Memory module"></div><div class="prod-name">NKV8 Refurbished</div><div class="price"><s>$255</s><b>$195</b></div><div class="add">Add To Cart</div></div>
</div>

<div class="abs strip" style="left:0;background:var(--teal)">
  <svg width="44" height="56" viewBox="0 0 44 56"><circle cx="22" cy="20" r="16" fill="none" stroke="#222" stroke-width="3"/><circle cx="22" cy="20" r="8" fill="none" stroke="#222" stroke-width="2"/><path d="M12 33l-4 20 8-5 6 6 0-18M32 33l4 20-8-5-6 6" fill="none" stroke="#222" stroke-width="3"/></svg>Warranty</div>
<div class="abs strip" style="left:400px;background:var(--lime)">
  <svg width="40" height="54" viewBox="0 0 40 54"><path d="M10 22V14a10 10 0 0 1 20 0v8" fill="none" stroke="#111" stroke-width="5"/><rect x="2" y="22" width="36" height="30" fill="#111"/><rect x="18" y="32" width="4" height="10" fill="var(--lime)"/></svg>Privacy Statement</div>
<div class="abs strip" style="left:800px;background:var(--peach)">
  <svg width="40" height="50" viewBox="0 0 40 50"><path d="M2 2h26l10 10v36H2z" fill="#fff" stroke="#1f6fb5" stroke-width="3"/><path d="M9 20h22M9 28h22M9 36h22" stroke="#1f6fb5" stroke-width="3"/></svg>Terms of Trade</div>

<footer class="abs footer">
  <div class="abs fcol" style="left:88px;width:230px">
    <h3>ABOUT US</h3>
    <p style="text-align:justify">Lorem Ipsum is simply dummy text of the printing and typesetting industry. Lorem Ipsum has been the industry's standard dummy text ever since the 1500s, when an unknown printer took a galley of type and scrambled it to make a type specimen book.</p>
    <p style="text-align:justify;margin-top:14px">It has survived not only five centuries, but also the leap into electronic typesetting, remaining essentially unchanged.</p>
  </div>
  <div class="abs fcol" style="left:358px;width:310px;font-size:11px">
    <h3>CONTACT US</h3>
    <div class="fline"><svg width="10" height="14" viewBox="0 0 10 14"><path d="M5 0a5 5 0 0 1 5 5c0 4-5 9-5 9S0 9 0 5a5 5 0 0 1 5-5z" fill="#333"/></svg>Unit 9 / 12 Tarrant St, Riverwood, NSW 2210</div>
    <div class="fline"><svg width="12" height="12" viewBox="0 0 24 24"><path d="M6 2l4 4-2 3c1 3 4 6 7 7l3-2 4 4-3 4C10 22 2 14 2 5z" fill="#333"/></svg>+61 2 5550 1427, 04 5550 2290</div>
    <div class="fline"><svg width="12" height="12" viewBox="0 0 12 12"><circle cx="6" cy="6" r="5" fill="none" stroke="#333" stroke-width="1.5"/><path d="M6 3v3h3" stroke="#333" fill="none"/></svg>8.30 am - 5.30 pm / Mon - Fri (UTC + 10)</div>
    <div class="fline"><svg width="12" height="9" viewBox="0 0 16 12"><rect width="16" height="12" fill="#333"/><path d="M0 0l8 7 8-7" fill="none" stroke="#fff"/></svg>sales@netkestrel.com.au</div>
    <div class="fline"><svg width="24" height="10"><rect width="24" height="10" rx="2" fill="#bbb"/></svg>http://stores.marketlane.com.au/netkestrel/</div>
  </div>
  <div class="abs fcol" style="left:690px">
    <h3>PAYMENT METHODS</h3>
    <div class="cards"><span></span><span></span><span></span><span></span><span></span></div>
  </div>
  <div class="abs fcol why" style="left:928px">
    <h3>WHY US</h3>
    <ul>
      <li><svg width="16" height="18" viewBox="0 0 16 18"><path d="M8 0l8 3v6c0 5-4 8-8 9-4-1-8-4-8-9V3z" fill="#888"/></svg>100% Wholesale Price</li>
      <li><svg width="16" height="18" viewBox="0 0 16 18"><path d="M8 0l8 3v6c0 5-4 8-8 9-4-1-8-4-8-9V3z" fill="#888"/></svg>100% Quality Assurance</li>
      <li><svg width="16" height="18" viewBox="0 0 16 18"><path d="M8 0l8 3v6c0 5-4 8-8 9-4-1-8-4-8-9V3z" fill="#888"/></svg>Free Support</li>
      <li><svg width="16" height="18" viewBox="0 0 16 18"><path d="M8 0l8 3v6c0 5-4 8-8 9-4-1-8-4-8-9V3z" fill="#888"/></svg>100% Money Back Guarantee</li>
      <li><svg width="16" height="18" viewBox="0 0 16 18"><path d="M8 0l8 3v6c0 5-4 8-8 9-4-1-8-4-8-9V3z" fill="#888"/></svg>Flexible Payment</li>
    </ul>
  </div>
  <div class="abs rule"></div>
  <div class="abs copy">Copyright © 2017, NetKestrel Pty Ltd. All rights reserved.</div>
</footer>

</body>
</html>
```